Alaska Law Firm Needs a Sticker Design

We need a design for stickers to put on already-printed brochures. We mail the brochures to potential clients so they can learn more about accident-induced injuries, insurance claims, legal representation, and our own law firm.

One of our lawyers wrote a book that provides a helpful overview of personal injury claims. We are offering this book for free to anyone who calls and requests it. Therefore, the sticker design should include one of the following phrases, or something very similar:
a) "Still have questions? Call and request our book-- for free!"
b) "Still have questions about auto accident claims? Call and request our book today."
c) "Still have questions about filing a claim? Call and request a free copy of our book."
d) "Still have questions? Call us today to request a free copy of our book, Clear Lanes Ahead."
e) "To learn more about automobile accidents and insurance, call today and request a free copy of our book."

The sticker should be approximately 3"x3" and may be a circle, square, rectangle, or ellipsis. The sticker will be placed on the back of the folder, which is light blue. We would like the sticker to match the color scheme of our website and the folder.

I will upload an image of the book cover as soon as I obtain it.

Law Firm

Font styles to use
Serif
Sans Serif

Requirements
Should not have
• Bright colors that aren't already used in the folder design. e.g. no bright orange, pink, chartreuse, turquoise, yellow, red.

```html
<!DOCTYPE html>
<html lang="en">
<head>
<meta charset="utf-8">
<title>Free Book Sticker</title>
<link rel="stylesheet" href="https://fonts.googleapis.com/css2?family=Inter:wght@700&family=Montserrat:wght@800&display=swap">
<style>
  :root {
    --sticker-blue: #CFE3F3;
    --edge-navy: #2A5C8F;
    --accent-navy: #1B4F82;
    --ink-deep: #0E2238;
    --page-bg: #FFFFFF;
  }
  html, body {
    margin: 0;
    padding: 0;
    width: 1200px;
    height: 1200px;
    overflow: hidden;
    background: var(--page-bg);
  }
  .sticker {
    position: relative;
    width: 1200px;
    height: 1200px;
  }
  .sticker-shape {
    position: absolute;
    inset: 0;
  }
  .message {
    position: absolute;
    top: 183px;
    left: 0;
    width: 1200px;
    margin: 0;
    text-align: center;
    font-family: "Inter", sans-serif;
    font-weight: 700;
    font-size: 87px;
    line-height: 93px;
    letter-spacing: -1px;
  }
  .message span { display: block; }
  .message .lead { color: var(--accent-navy); }
  .message .call-to-action { color: var(--ink-deep); }
  .divider-dots {
    position: absolute;
    top: 861px;
    left: 505px;
    display: flex;
    gap: 75px;
  }
  .divider-dots i {
    display: block;
    width: 12px;
    height: 12px;
    border-radius: 50%;
    background: var(--edge-navy);
  }
  .phone-line {
    position: absolute;
    top: 915px;
    left: 0;
    width: 1200px;
    display: flex;
    justify-content: center;
    align-items: center;
    gap: 26px;
    color: var(--accent-navy);
  }
  .phone-icon { width: 74px; height: 74px; }
  .phone-number {
    font-family: "Montserrat", sans-serif;
    font-weight: 800;
    font-size: 86px;
    letter-spacing: 1px;
    line-height: 1;
  }
</style>
</head>
<body>
<div class="sticker">
  <svg class="sticker-shape" width="1200" height="1200" viewBox="0 0 1200 1200" aria-hidden="true">
    <circle cx="600" cy="600" r="598" fill="var(--sticker-blue)"/>
    <circle cx="600" cy="600" r="573" fill="none" stroke="var(--edge-navy)" stroke-width="8" stroke-dasharray="1.6 4.4"/>
    <circle cx="600" cy="600" r="573" fill="none" stroke="var(--edge-navy)" stroke-width="1.2"/>
  </svg>

  <p class="message">
    <span class="lead">To learn more</span>
    <span class="lead">about automobile</span>
    <span class="lead">accidents</span>
    <span class="lead">and insurance,</span>
    <span class="call-to-action">Call today and</span>
    <span class="call-to-action">request a free copy</span>
    <span class="call-to-action">of our book.</span>
  </p>

  <div class="divider-dots" aria-hidden="true"><i></i><i></i><i></i></div>

  <div class="phone-line">
    <svg class="phone-icon" viewBox="0 0 74 74" aria-hidden="true">
      <circle cx="37" cy="37" r="33" fill="none" stroke="currentColor" stroke-width="4"/>
      <path d="M46 16 l8 6 c2 2 2 4 0 6 l-5 5 c-1 1 -3 1 -4 0 l-3 -3 c-5 4 -9 10 -11 17 l4 2 c1 1 2 2 1 4 l-3 7 c-1 2 -3 3 -5 2 l-9 -4 c-1 -14 8 -32 21 -42 c2 -1 4 -1 6 0 z" fill="currentColor"/>
    </svg>
    <span class="phone-number">907.555.0142</span>
  </div>
</div>
</body>
</html>
```